Turm7Zwerge
Zielgruppe
Zielgruppe sind die Eltern, Lehrer, Kindergärtner, aber auch Kinder, die bereits Lesen können.
Aufgabenstellung
Ich brauche einen Flyer und ein Plakat für eine Kinderschachschule für Kinder zwischen 4 und 15 Jahren. Auf dem Flyer, den ich in A6-Format drucken möchte (beidseitig), muss ich die Info über die Kinderschachschule Turm7Zwerge (mehr Infos unter www.turm7zwerge-beispiel.ch), dh., was wir machen, Kontaktdaten, etc schreiben können. Es dient als Werbematerial zum Auslegen
Auf dem Plakat wird mehr oder weniger das Gleiche stehen, es wird jedoch als Din A4 Seite aufgehängt.
Unsere Kontaktinformation ist wie folgt:
Turm7Zwerge: Züge für Wolkenkinder
www.turm7zwerge-beispiel.ch

```html
<!DOCTYPE html>
<html lang="de">
<head>
<meta charset="utf-8">
<title>Turm7Zwerge – Züge für Wolkenkinder</title>
<link href="https://fonts.googleapis.com/css2?family=Signika:wght@300;400;600;700&display=swap" rel="stylesheet">
<style>
  :root {
    --ink: #1f1f1f;
    --text: #2b2b2b;
    --blue: #2f8fd0;
    --magenta: #c8197f;
    --gold: #c9a126;
    --band: #c29a1c;
    --floor-light: #ffffff;
    --floor-grey: #ebebeb;
    --photo-dark: #2a2e36;
    --photo-mid: #6b6a66;
    --logo: #c8197f;
  }
  * { margin: 0; padding: 0; box-sizing: border-box; }
  html, body { width: 1200px; height: 1200px; overflow: hidden; background: #fff; }
  .flyer {
    position: relative; width: 1200px; height: 1200px; overflow: hidden;
    font-family: "Signika", Arial, sans-serif; color: var(--text); background: var(--floor-light);
  }
  .floor {
    position: absolute; left: 0; top: 250px; width: 1200px; height: 800px;
    background: linear-gradient(180deg, rgba(235,235,235,0) 0%, var(--floor-grey) 45%, #f4f4f4 100%);
  }
  .section-title {
    position: absolute; left: 81px; font-weight: 600; font-size: 26px; color: var(--ink);
    display: flex; align-items: center; gap: 14px; white-space: nowrap;
  }
  .title-mark { width: 30px; height: 30px; border-radius: 50%; display: inline-block; }
  .swoosh { position: absolute; left: 40px; width: 420px; height: 30px; }
  .copy {
    position: absolute; left: 81px; font-size: 20px; line-height: 30.5px; font-weight: 400; color: var(--text);
  }
  .logo {
    position: absolute; left: 868px; top: 60px; width: 290px; text-align: center;
  }
  .logo-dot { width: 90px; height: 90px; margin: 0 auto 12px; background: var(--logo); opacity: .9; }
  .logo-name { font-size: 40px; font-weight: 700; color: var(--logo); line-height: 1; }
  .logo-tag { font-size: 20px; font-weight: 600; color: var(--ink); margin-top: 6px; }
  .photo {
    position: absolute; left: 797px; top: 594px; width: 369px; height: 234px;
    background: linear-gradient(120deg, var(--photo-dark) 0%, var(--photo-mid) 55%, #3a3c40 100%);
  }
  .contact-band {
    position: absolute; left: 0; top: 1044px; width: 1200px; height: 156px; background: var(--band);
    color: #fff; font-size: 20px;
  }
  .contact-band span { position: absolute; white-space: nowrap; }
  .contact-label { font-weight: 700; }
</style>
</head>
<body>
<main class="flyer">
  <div class="floor" role="img" aria-label="Heller, perspektivischer Schachbrettboden als Hintergrund"></div>

  <div class="logo">
    <div class="logo-dot"></div>
    <div class="logo-name">Turm7Zwerge</div>
    <div class="logo-tag">Züge für Wolkenkinder</div>
  </div>

  <svg class="swoosh" style="top:72px" viewBox="0 0 420 30"><path d="M2 22 Q150 4 420 8 Q160 12 2 22Z" fill="var(--blue)"/></svg>
  <h2 class="section-title" style="top:44px">Warum Schach für Kinder <i class="title-mark" style="border:3px solid var(--blue)"></i></h2>
  <p class="copy" style="top:96px; width:770px">Schach ist weit mehr als ein weiteres Angebot im Dschungel der Kurs-<br>angebote für Kinder. Schach ist eine Lebensschule, die das Leben Ihres<br>Kindes nachhaltig zum Positiven beeinflusst. Die Kinder eignen sich<br>spielerisch wesentliche Fähigkeiten an, die sie sowohl im sozialen als auch<br>im schulischen Umfeld zu Höchstleistungen befähigen.</p>

  <svg class="swoosh" style="top:322px" viewBox="0 0 420 30"><path d="M2 22 Q150 4 420 8 Q160 12 2 22Z" fill="var(--magenta)"/></svg>
  <h2 class="section-title" style="top:294px">Schach macht Spass! <i class="title-mark" style="background:var(--magenta)"></i></h2>
  <p class="copy" style="top:356px; width:1130px">Schach zieht jeden Spieler sofort in seinen Bann: Kaum ist das Schachbrett aufgebaut und der erste Zug<br>getan, beginnt die Magie zu wirken: Vor den Kindern liegt ein Meer voller aufregender Geschichten.<br>Die spannenden Figuren und intensiven Kämpfe um Sieg und Niederlage wecken den Abenteuergeist der<br>Kinder, ihre Phantasie wird angeregt und lässt die Kinder nicht mehr los. An Spannung schlägt Schach<br>jedes Computerspiel!</p>

  <svg class="swoosh" style="top:574px" viewBox="0 0 420 30"><path d="M2 22 Q150 4 420 8 Q160 12 2 22Z" fill="var(--gold)"/></svg>
  <h2 class="section-title" style="top:546px">Schach macht schlau und aufmerksam! <i class="title-mark" style="background:var(--gold)"></i></h2>
  <p class="copy" style="top:612px; width:700px">Schach ist Magie: Kaum ist das Schachbrett aufgebaut und der<br>erste Zug getan, liegt vor den Kindern ein Meer voller aufregender<br>Geschichten.<br>Die spannenden Figuren und intensiven Kämpfe um Sieg und<br>Niederlage wecken den Abenteuergeist der Kinder, ihre Phantasie<br>wird angeregt und lässt die Kinder nicht mehr los. An Spannung<br>schlägt Schach jedes Computerspiel!</p>
  <div class="photo" role="img" aria-label="Foto: zwei Kinder spielen an einem Tisch eine Partie Schach"></div>

  <svg class="swoosh" style="top:904px" viewBox="0 0 420 30"><path d="M2 22 Q150 4 420 8 Q160 12 2 22Z" fill="var(--blue)"/></svg>
  <h2 class="section-title" style="top:876px">Schach macht stark und selbstbewusst! <i class="title-mark" style="border:3px solid var(--blue)"></i></h2>
  <p class="copy" style="top:936px; width:1120px">Schach ist lebensnah und vermittelt den Kindern, mit Herausforderungen im Leben konstruktiv<br>umzugehen. Der Umgang mit Erfolgen und Niederlagen hilft, ihr Selbstvertrauen und psychische<br>Stabilität zu stärken.</p>

  <footer class="contact-band">
    <span class="contact-label" style="left:81px; top:30px">Unsere Kontaktdaten:</span>
    <span style="left:367px; top:30px">Turm7Zwerge</span>
    <span style="left:367px; top:61px">Lindenweg 12</span>
    <span style="left:367px; top:92px">Postfach 418</span>
    <span style="left:606px; top:92px">8799 Bergwil</span>
    <span style="left:837px; top:30px">Tel. 079 000 12 34</span>
    <span style="left:837px; top:61px">info@turm7zwerge-beispiel.ch</span>
    <span style="left:837px; top:92px">www.turm7zwerge-beispiel.ch</span>
  </footer>
</main>
</body>
</html>
```